Business card design for sustainable building and development company

Need a business card design for a new sustainable building and real estate development company in the San Francisco Bay area. Name of company is "Tovrin Advisors, LLC" and we provide "Sustainable building, energy and development services" for residential and non residential projects. We'd like the following colors used but not all area required: green, gray, blue. Design should communicate innovation, professionalism and sustainability. Our current website is www.tovrin-advisors.example. Another possible design idea is to have the following listed on the back of the card:
Certified: VERN QS, Eco Marker Rater, DOLM Rater, Terravue Inspector, KSO TQ Building Analyst. Its not a must but could be text that could be used for back of card. Overall, we are open to a simple, clean design and or one with more text than usual for a card.

Industry/Entity Type

Real Estate

Contact Information for Business Card

Name on card: Mark J. Halvik
Title for Name: Principal + Founder
Phone: 555.814.0627
Email: mhalvik@tovrin-advisors.example
Website: www.tovrin-advisors.example

Also, please add the following for address:
San Francisco, California

Requirements
Nice to have
• If you can integrate the outline of a skyline on the backside of the card and if it looks good, I would like to see the design
Should not have
• a barcode;

```html
<!DOCTYPE html>
<html lang="en">
<head>
<meta charset="utf-8">
<title>Tovrin Advisors — Business Card</title>
<link rel="stylesheet" href="https://fonts.googleapis.com/css2?family=Montserrat:wght@700&family=Open+Sans:wght@400;600&display=swap">
<style>
  :root {
    --green: #6cbd4b;
    --green-deep: #5aa83c;
    --ink: #2a2a2a;
    --black: #1c1c1c;
    --paper: #f4f4f4;
    --paper-shade: #e6e6e6;
    --backdrop: #c9cdd2;
    --white: #ffffff;
  }
  * { margin: 0; padding: 0; box-sizing: border-box; }
  html, body { width: 1200px; height: 866px; overflow: hidden; }
  body {
    background: var(--backdrop);
    font-family: "Open Sans", Arial, sans-serif;
    position: relative;
  }
  .card {
    position: absolute;
    top: 278px;
    width: 540px;
    height: 309px;
    background: linear-gradient(135deg, var(--white), var(--paper) 60%, var(--paper-shade));
    overflow: hidden;
    box-shadow: 0 6px 18px rgba(0,0,0,0.18);
  }
  .card--front { left: 40px; }
  .card--back { left: 620px; }

  /* Front */
  .front__illustration {
    position: absolute;
    left: 0; bottom: 0;
    width: 210px; height: 170px;
    background: linear-gradient(160deg, var(--green), var(--green-deep));
    border-top-right-radius: 170px;
  }
  .front__brand {
    position: absolute;
    left: 240px; top: 112px;
  }
  .brand-name {
    font-family: "Montserrat", Arial, sans-serif;
    font-weight: 700;
    color: var(--green);
    letter-spacing: -0.5px;
    line-height: 1;
    white-space: nowrap;
  }
  .front__brand .brand-name { font-size: 34px; }
  .tagline {
    font-family: "Open Sans", Arial, sans-serif;
    font-size: 8.5px;
    font-weight: 400;
    color: var(--ink);
    text-transform: uppercase;
    letter-spacing: 0.1px;
    margin-top: 5px;
    white-space: nowrap;
  }

  /* Back */
  .back__shapes { position: absolute; inset: 0; }
  .back__logo {
    position: absolute;
    left: 40px; top: 118px;
    width: 175px;
    text-align: center;
  }
  .logo-dot {
    display: block;
    width: 44px; height: 44px;
    margin: 0 auto 8px;
    border-radius: 50%;
    background: var(--green);
  }
  .back__logo .brand-name { font-size: 19px; }
  .back__logo .tagline { font-size: 5px; margin-top: 3px; }
  .contact {
    position: absolute;
    right: 26px; top: 30px;
    text-align: right;
    color: var(--white);
    font-size: 12.5px;
    line-height: 1.35;
    white-space: nowrap;
  }
  .contact__name { font-weight: 600; font-size: 14px; }
  .contact__title { margin-bottom: 38px; font-size: 14px; }
  .contact__address { margin-bottom: 12px; }
  .contact__line { display: flex; justify-content: flex-end; align-items: center; gap: 6px; }
  .contact__line svg { width: 10px; height: 10px; fill: var(--white); flex: none; }
  .contact__web { margin-top: 6px; }
</style>
</head>
<body>

  <section class="card card--front">
    <div class="front__illustration" role="img" aria-label="Green building illustration"></div>
    <div class="front__brand">
      <div class="brand-name">Tovrin Advisors</div>
      <div class="tagline">Sustainable Building, Energy &amp; Development Services</div>
    </div>
  </section>

  <section class="card card--back">
    <svg class="back__shapes" viewBox="0 0 540 309" width="540" height="309" aria-hidden="true">
      <path d="M225 0 H540 V309 H165 C285 235 300 95 225 0 Z" fill="var(--green)"/>
      <path d="M225 0 C300 95 285 235 165 309" fill="none" stroke="var(--white)" stroke-width="5"/>
      <path d="M178 309 C270 235 288 140 258 70 C300 150 290 240 220 309 Z" fill="var(--black)"/>
    </svg>

    <div class="back__logo">
      <span class="logo-dot"></span>
      <div class="brand-name">Tovrin Advisors</div>
      <div class="tagline">Sustainable Building, Energy &amp; Development Services</div>
    </div>

    <div class="contact">
      <div class="contact__name">Mark J. Halvik</div>
      <div class="contact__title">Principal + Founder</div>
      <div class="contact__address">San Francisco,<br>California</div>
      <div class="contact__line">555.814.0627
        <svg viewBox="0 0 10 10"><path d="M2 0.5 L3.8 2.6 3 3.6 C3.6 5 5 6.4 6.4 7 L7.4 6.2 9.5 8 8.3 9.5 C4.5 9.2 0.8 5.5 0.5 1.7 Z"/></svg>
      </div>
      <div class="contact__line">555.814.0628
        <svg viewBox="0 0 10 10"><rect x="1" y="3" width="8" height="6"/><rect x="3" y="0.5" width="4" height="3"/></svg>
      </div>
      <div class="contact__line">mhalvik@tovrin-advisors.example
        <svg viewBox="0 0 10 10"><path d="M0.5 2 H9.5 V8 H0.5 Z M0.5 2 L5 5.5 9.5 2" fill="none" stroke="#fff" stroke-width="1"/></svg>
      </div>
      <div class="contact__web">www.tovrin-advisors.example</div>
    </div>
  </section>

</body>
</html>
```